Business Card for beauty technology startup

Design Glimora Business Card for a Beauty, based on the website identity and colors (https://www.glimora-example.com).
Glimora is a beauty tech startup that gathers helpful product info for beauty lovers and consumers (such as availability on stores, price range and product reviews) for makeup products. The card design must be young, colorful but clean, and very modern.

Target Market(s)

woman, 15-35

Industry/Entity Type

Cosmetics

Contact Information for Business Card

Full Name, address, phone

Font styles to use
Other font styles liked:
• Advent Pro

Colors
e34297
86cfc6
ffffff
5c5c5c
e8e8e8
e667a6
b2b2b2

Requirements
Must have
• One full colored side with a creative design and another with card info
• Use Color palette: #95C5C5 and/or #D38AA5
• Use fonts: Advent Pro
• Use website identity: https://www.glimora-example.com
Nice to have
• If needed extra font: Roboto

```html
<!DOCTYPE html>
<html lang="en">
<head>
<meta charset="utf-8">
<title>Glimora Business Card</title>
<link href="https://fonts.googleapis.com/css2?family=Roboto:wght@300;400;700&display=swap" rel="stylesheet">
<style>
  :root {
    --backdrop: #3b3b3d;
    --card: #1f1e22;
    --card-edge: #2a2930;
    --pink: #e34297;
    --pink-soft: #e667a6;
    --teal-bright: #86cfc6;
    --white: #ffffff;
    --rose: #c98bab;
    --rose-muted: #a9728f;
    --teal: #74b3ac;
  }
  * { margin: 0; padding: 0; box-sizing: border-box; }
  html, body {
    width: 799px;
    height: 1200px;
    overflow: hidden;
    background: var(--backdrop);
    font-family: "Roboto", sans-serif;
  }
  .sheet {
    position: relative;
    width: 799px;
    height: 1200px;
  }
  .card {
    position: absolute;
    left: 90px;
    width: 620px;
    height: 354px;
    border-radius: 4px;
    overflow: hidden;
    box-shadow: 0 14px 30px rgba(0, 0, 0, 0.45);
  }
  .card--front {
    top: 123px;
    background: linear-gradient(135deg, var(--pink) 0%, var(--pink-soft) 45%, var(--teal-bright) 100%);
  }
  .card--back {
    top: 723px;
    background: var(--card);
    border: 1px solid var(--card-edge);
  }

  .front-lines {
    position: absolute;
    inset: 0;
    width: 100%;
    height: 100%;
  }
  .front-lines path {
    fill: none;
    stroke: var(--white);
    stroke-width: 1.5;
    opacity: 0.35;
  }
  .front-mark {
    position: absolute;
    inset: 0;
    display: flex;
    align-items: center;
    justify-content: center;
    gap: 18px;
  }
  .front-mark__dot {
    width: 20px;
    height: 20px;
    border-radius: 50%;
    background: var(--white);
  }
  .front-mark__name {
    font-weight: 300;
    font-size: 56px;
    letter-spacing: 8px;
    color: var(--white);
    text-transform: uppercase;
  }

  .brand {
    position: absolute;
    top: 58px;
    right: 44px;
    display: flex;
    align-items: center;
    gap: 12px;
  }
  .brand__dot {
    width: 30px;
    height: 30px;
    border-radius: 50%;
    border: 1.5px solid var(--rose-muted);
  }
  .brand__name {
    font-weight: 300;
    font-size: 30px;
    letter-spacing: 5px;
    color: var(--rose-muted);
    text-transform: uppercase;
  }

  .contact {
    position: absolute;
    left: 40px;
    top: 180px;
    color: var(--rose);
  }
  .contact__name {
    font-weight: 700;
    font-size: 22px;
    letter-spacing: 0.5px;
    text-transform: uppercase;
    margin-bottom: 10px;
  }
  .contact__row {
    display: flex;
    align-items: center;
    gap: 10px;
    font-size: 15px;
    line-height: 23px;
  }
  .contact__icon {
    width: 14px;
    height: 14px;
    flex: none;
    stroke: var(--teal);
    fill: none;
    stroke-width: 1.6;
    stroke-linecap: round;
    stroke-linejoin: round;
  }
  .contact__address {
    font-size: 15px;
    line-height: 23px;
    margin-top: 4px;
  }
</style>
</head>
<body>
<main class="sheet">
  <section class="card card--front" aria-label="Card front">
    <svg class="front-lines" viewBox="0 0 620 354" preserveAspectRatio="none" aria-hidden="true">
      <path d="M0 300 C160 240 300 330 620 220"/>
      <path d="M0 80 C200 20 380 120 620 40"/>
    </svg>
    <div class="front-mark">
      <span class="front-mark__dot"></span>
      <span class="front-mark__name">Glimora</span>
    </div>
  </section>

  <section class="card card--back" aria-label="Card back">
    <div class="brand">
      <span class="brand__dot"></span>
      <span class="brand__name">Glimora</span>
    </div>

    <div class="contact">
      <p class="contact__name">Maya Lindqvist</p>
      <p class="contact__row">
        <svg class="contact__icon" viewBox="0 0 16 16"><path d="M3 1.5h3l1.5 3.5-2 1.3a8 8 0 0 0 4.2 4.2l1.3-2 3.5 1.5v3a1.5 1.5 0 0 1-1.5 1.5A12.5 12.5 0 0 1 1.5 3 1.5 1.5 0 0 1 3 1.5z"/></svg>
        00 444 555 666
      </p>
      <p class="contact__row">
        <svg class="contact__icon" viewBox="0 0 16 16"><path d="M6.5 9.5l3-3"/><path d="M7 4.5l1.5-1.5a2.8 2.8 0 0 1 4 4L11 8.5"/><path d="M9 11.5L7.5 13a2.8 2.8 0 0 1-4-4L5 7.5"/></svg>
        www.glimora-example.com
      </p>
      <p class="contact__row">
        <svg class="contact__icon" viewBox="0 0 16 16"><rect x="1.5" y="3.5" width="13" height="9" rx="1"/><path d="M1.5 4.5L8 9l6.5-4.5"/></svg>
        yourname@glimora-example.com
      </p>
      <p class="contact__address">123, Street Number, City Name, Country - 123456</p>
    </div>
  </section>
</main>
</body>
</html>
```